UK landscaping company needs website

We, Brackwell Landscapes need a website design for a company based in Surrey, UK. The design should be bold and playful. We have three main areas of work driveways, paving and fencing. It shouldn't be too heavy in text and concentrate on the pictures from previous jobs we've completed. You may use stock images for the design, these can be changed if you are successful. Please don’t just copy the flyer it is just there to provide content.
We have a logo design which we would also like editing slightly.
Here are some of my local competitors
https://www.pelmarlandscapes.example.co.uk/

https://www.twinfirgardendesign.example.com/

https://kestbyrnlandscapes.example.co.uk/

Industry/Entity Type

Landscaping

Coding

Coded - Design and coding required

Number of Pages Required

3 page

Font styles to use
Sans Serif

Requirements
Must have
• Pictures of my previous jobs.
Must be mobile friendly
Easy to navigate
Nice to have
• Try to use different colours. It would be good to have some designs that aren’t just black and green.
I’d like some curves in the design.
Should not have
• We install hard landscaping. Think more building/construction and less plants and cutting grass.

```html
<!DOCTYPE html>
<html lang="en">
<head>
<meta charset="utf-8">
<title>Brackwell Landscapes</title>
<link href="https://fonts.googleapis.com/css2?family=Poppins:wght@600;700;800&family=Roboto:ital,wght@0,400;0,500;1,400;1,500&display=swap" rel="stylesheet">
<style>
:root{
  --green:#5ab52f;
  --green-dark:#3f8f1c;
  --green-pale:#eef8e7;
  --black:#000;
  --ink:#1c1c1c;
  --grey:#555;
  --line:#9a9a9a;
  --white:#fff;
}
*{box-sizing:border-box;margin:0;padding:0}
html,body{width:1200px;height:3661px;overflow:hidden;background:var(--white)}
body{position:relative;font-family:'Roboto',sans-serif;color:var(--ink)}
.abs{position:absolute}

/* header */
.site-header{left:0;top:0;width:1200px;height:80px;background:var(--black)}
.brand{left:144px;top:22px;color:var(--white);font:700 22px/1 'Poppins',sans-serif;letter-spacing:.5px;text-transform:uppercase}
.brand small{display:block;font-size:11px;letter-spacing:2px;margin-top:4px}
.main-nav{left:424px;top:33px;display:flex;gap:38px;font:500 12.5px/1 'Roboto',sans-serif;color:var(--white)}
.main-nav .active{border-bottom:2px solid var(--green);padding-bottom:5px}
.header-phone{left:896px;top:29px;color:var(--green);font:500 19px/1 'Roboto',sans-serif;display:flex;align-items:center;gap:10px}

/* hero */
.hero-photo{left:0;top:80px;width:1200px;height:602px;background:linear-gradient(180deg,#c49a63 0%,#b78a55 25%,#3e5a2a 45%,#2e4a1f 65%,#9a8a78 100%)}
.hero-title{left:0;top:190px;width:1200px;text-align:center;color:var(--white);font:800 72px/82px 'Poppins',sans-serif;text-transform:uppercase}
.hero-arrow{top:296px;width:38px;height:38px;border-radius:50%;background:#1a1a1a;display:flex;align-items:center;justify-content:center}
.btn{display:flex;align-items:center;justify-content:center;border:2px solid var(--green);font:500 19px/1 'Roboto',sans-serif;text-transform:uppercase;color:var(--green);background:transparent}
.btn-hero{left:505px;top:381px;width:190px;height:46px;color:var(--white);background:rgba(0,0,0,.35)}
.hero-curve{left:0;top:560px}

.service{border-radius:50%;border:5px solid var(--green);border-top:none;display:flex;align-items:flex-end;justify-content:center;color:var(--white);font:500 20px/1 'Roboto',sans-serif;text-transform:uppercase}
.service-driveways{left:220px;top:519px;width:256px;height:256px;padding-bottom:58px;background:radial-gradient(circle at 50% 40%,#7f7f83,#3a3a3e)}
.service-paving{left:443px;top:487px;width:312px;height:312px;padding-bottom:68px;background:radial-gradient(circle at 50% 40%,#a59585,#4a403a)}
.service-fencing{left:722px;top:519px;width:256px;height:256px;padding-bottom:58px;background:radial-gradient(circle at 50% 30%,#8fa1c4 0%,#6f5f43 45%,#2e2a22 100%)}

/* section headings */
.heading{left:0;width:1200px;text-align:center;font:700 42px/1.36 'Poppins',sans-serif;text-transform:uppercase;color:var(--ink)}
.heading .accent{color:var(--green)}
.swoosh{left:563px}

/* welcome */
.welcome-text{left:210px;top:1050px;width:780px;text-align:center;font:400 14px/27px 'Roboto',sans-serif;color:var(--grey)}
.btn-more{left:520px;top:1193px;width:160px;height:47px}

/* projects */
.projects-band{left:0;top:1322px;width:1200px;height:136px;background:var(--green-pale)}
.project-grid{left:7px;top:1467px;display:grid;grid-template-columns:repeat(5,230px);grid-auto-rows:307px;gap:10px 9px}
.project{display:block}
.p1{background:linear-gradient(180deg,#4d6a33 0%,#56722f 47%,#8a6a3a 50%,#6a5234 100%)}
.p2{background:linear-gradient(160deg,#6d5442,#8a7260 45%,#a7a7aa 70%,#8f8f93)}
.p3{background:linear-gradient(180deg,#6f5a44 0%,#5b4533 50%,#4f7d2a 62%,#b8ab9a 100%)}
.p4{background:linear-gradient(180deg,#a9c4e6 0%,#c9b08a 35%,#7a6a58 60%,#cfc9c3 100%)}
.p5{background:linear-gradient(180deg,#9cc0e0 0%,#6b5b4a 30%,#9a8255 55%,#4f8d2d 100%)}
.p6{background:linear-gradient(180deg,#3c4a2a 0%,#4a5a35 48%,#4f7a30 52%,#3f7a28 100%)}
.p7{background:linear-gradient(180deg,#8a6a4a 0%,#a98458 45%,#5a8a35 60%,#d8ccb6 100%)}
.p8{background:linear-gradient(180deg,#e7e7e7 0%,#6d6d70 40%,#3c3c40 70%,#9a9a98 100%)}
.p9{background:linear-gradient(180deg,#f0ede6 0%,#a29a90 40%,#b6968a 70%,#c9b7a4 100%)}
.p10{background:linear-gradient(180deg,#5b5346 0%,#3fa8d8 30%,#2a90c8 45%,#c6a487 70%,#bd9577 100%)}
.btn-load{left:520px;top:2141px;width:160px;height:47px}

/* testimonials */
.testimonial-bg{left:0;top:2197px}
.testimonial-heading{color:var(--white);top:2374px}
.quote-mark{left:569px;top:2500px}
.testimonial-text{left:200px;top:2583px;width:800px;text-align:center;color:var(--white);font:italic 400 14px/27px 'Roboto',sans-serif}
.testimonial-name{left:0;top:2684px;width:1200px;text-align:center;color:var(--white);font:italic 400 14px/1 'Roboto',sans-serif}
.testimonial-name b{font-style:normal;font-weight:500}
.slide-arrow{top:2596px}

/* contact */
.contact-form{left:233px;top:3018px;width:733px;display:grid;grid-template-columns:1fr 1fr;gap:11px 10px}
.field{height:55px;border:1px solid var(--line);padding:0 21px;display:flex;align-items:center;font:400 14px/1 'Roboto',sans-serif;color:#444}
.field-message{grid-column:1 / 3;height:116px;align-items:flex-start;padding-top:20px}
.grass{left:0;top:3300px;width:1200px;height:131px;background:linear-gradient(180deg,rgba(255,255,255,0) 0%,#b8e08c 30%,#6dbb38 65%,#3c8d1e 100%)}
.btn-submit{left:489px;top:3304px;width:222px;height:47px;z-index:2;background:rgba(255,255,255,.6)}

/* footer */
.site-footer{left:0;top:3431px;width:1200px;height:230px;background:var(--black)}
.footer-brand{left:142px;top:3478px;color:var(--white);font:700 56px/1 'Poppins',sans-serif;text-transform:uppercase}
.footer-brand small{display:block;font-size:22px;letter-spacing:3px;margin-top:8px;text-align:right}
.footer-nav{left:545px;top:3489px;color:var(--white);font:500 16.5px/1 'Roboto',sans-serif;display:flex;gap:12px}
.footer-copy{left:545px;top:3534px;color:var(--white);font:400 13px/1 'Roboto',sans-serif}
.social{left:545px;top:3582px;display:flex;gap:12px}
.social span{width:20px;height:20px;border-radius:50%;background:var(--white)}
</style>
</head>
<body>

<header class="abs site-header">
  <div class="abs brand">Brackwell<small>Landscapes</small></div>
  <nav class="abs main-nav">
    <span class="active">HOME</span><span>ABOUT US</span><span>SERVICES</span><span>GALLERY</span><span>CONTACT US</span>
  </nav>
  <div class="abs header-phone">
    <svg width="18" height="18" viewBox="0 0 24 24"><path fill="#5ab52f" d="M6.6 10.8a15.1 15.1 0 0 0 6.6 6.6l2.2-2.2a1 1 0 0 1 1-.25 11.4 11.4 0 0 0 3.6.57 1 1 0 0 1 1 1V20a1 1 0 0 1-1 1A17 17 0 0 1 3 4a1 1 0 0 1 1-1h3.5a1 1 0 0 1 1 1c0 1.25.2 2.45.57 3.57a1 1 0 0 1-.25 1z"/></svg>
    07700 900 418
  </div>
</header>

<section class="hero">
  <div class="abs hero-photo" role="img" aria-label="Photo of a finished garden with timber decking, sleeper steps, artificial lawn and sandstone patio"></div>
  <h1 class="abs hero-title">Brackwell<br>Landscapes</h1>
  <div class="abs hero-arrow" style="left:52px"><svg width="12" height="12" viewBox="0 0 12 12"><path d="M8 1L3 6l5 5" stroke="#fff" stroke-width="2" fill="none"/></svg></div>
  <div class="abs hero-arrow" style="left:1110px"><svg width="12" height="12" viewBox="0 0 12 12"><path d="M4 1l5 5-5 5" stroke="#fff" stroke-width="2" fill="none"/></svg></div>
  <a class="abs btn btn-hero">Get Started</a>
  <svg class="abs hero-curve" width="1200" height="122" viewBox="0 0 1200 122">
    <path d="M0 122 L0 120 Q600 -20 1200 120 L1200 122 Z" fill="#fff"/>
    <path d="M0 120 Q600 -20 1200 120" stroke="#5ab52f" stroke-width="5" fill="none"/>
  </svg>
  <div class="abs service service-driveways" role="img" aria-label="Photo of a grey slab driveway">Driveways</div>
  <div class="abs service service-fencing" role="img" aria-label="Photo of a timber panel fence">Fencing</div>
  <div class="abs service service-paving" role="img" aria-label="Photo of a circular paving feature">Paving</div>
</section>

<section class="welcome">
  <h2 class="abs heading" style="top:878px"><span class="accent">Welcome to</span><br>Brackwell Landscapes</h2>
  <svg class="abs swoosh" style="top:1002px" width="74" height="22" viewBox="0 0 74 22"><path d="M2 20 Q30 2 72 4 Q34 6 2 20Z" fill="#5ab52f"/></svg>
  <p class="abs welcome-text">Lorem ipsum dolor sit amet, consectetur adipiscing elit, sed do eiusmod tempor incididunt ut labore et dolore magna aliquauis ipsum suspendisse ultrius commodo viverra maecenas accumsan lacus vel facilisis. Lorem ipsum dolor sit amet, consectetur adipiscing elit, sed do eiusmod tempor incididunt ut labore et dolore magna aliquauis ipsum suspendisse ultrius commodo viverra maecenas accumsan laum dolor sit amet, consectetur adipiscing elit</p>
  <a class="abs btn btn-more">Read More</a>
</section>

<section class="projects">
  <div class="abs projects-band"></div>
  <h2 class="abs heading" style="top:1355px"><span class="accent">Our</span> Projects</h2>
  <svg class="abs swoosh" style="top:1422px" width="74" height="22" viewBox="0 0 74 22"><path d="M2 20 Q30 2 72 4 Q34 6 2 20Z" fill="#5ab52f"/></svg>
  <div class="abs project-grid">
    <div class="project p1" role="img" aria-label="Project photo: lawn and new feather-edge fence"></div>
    <div class="project p2" role="img" aria-label="Project photo: trellis fencing and grey patio"></div>
    <div class="project p3" role="img" aria-label="Project photo: fence, raised lawn and sandstone patio"></div>
    <div class="project p4" role="img" aria-label="Project photo: timber pergola over patio"></div>
    <div class="project p5" role="img" aria-label="Project photo: close-board fence beside lawn"></div>
    <div class="project p6" role="img" aria-label="Project photo: garden before and after new lawn"></div>
    <div class="project p7" role="img" aria-label="Project photo: artificial lawn and patio"></div>
    <div class="project p8" role="img" aria-label="Project photo: block paved curved step"></div>
    <div class="project p9" role="img" aria-label="Project photo: circular paving by summerhouse"></div>
    <div class="project p10" role="img" aria-label="Project photo: swimming pool with sandstone surround"></div>
  </div>
  <a class="abs btn btn-load">Load More</a>
</section>

<section class="testimonials">
  <svg class="abs testimonial-bg" width="1200" height="682" viewBox="0 0 1200 682" role="img" aria-label="Green tinted photo of a garden fence and trees">
    <defs><linearGradient id="tg" x1="0" y1="0" x2="0" y2="1"><stop offset="0" stop-color="#62bb32"/><stop offset=".5" stop-color="#56ad2b"/><stop offset="1" stop-color="#4c9e26"/></linearGradient></defs>
    <path d="M0 0 Q600 178 1200 0 L1200 682 Q600 498 0 682 Z" fill="url(#tg)"/>
  </svg>
  <h2 class="abs heading testimonial-heading">Client Testimonials</h2>
  <svg class="abs swoosh" style="top:2440px" width="74" height="22" viewBox="0 0 74 22"><path d="M2 20 Q30 2 72 4 Q34 6 2 20Z" fill="#fff"/></svg>
  <svg class="abs quote-mark" width="62" height="62" viewBox="0 0 62 62"><path d="M31 4a26 24 0 1 0 14 44l10 8-3-13A24 24 0 0 0 31 4z" fill="none" stroke="#fff" stroke-width="3"/><text x="31" y="44" text-anchor="middle" font-family="Poppins,sans-serif" font-weight="700" font-size="34" fill="#fff">”</text></svg>
  <p class="abs testimonial-text">Lorem ipsum dolor sit amet, consectetur adipiscing elit, sed do eiusmod tempor incididunt ut labore et dolore magna aliquauis ipsum suspendisse ultrices gravida. Risus commodo viverra maecenas accumsan lacus vel facilisis. Lorem ipsum dolor sit amet, consectetur adipiscing elit, sed do eiusmod tempor incididunt ut labore et dolore magnisse ultrices graviverra</p>
  <p class="abs testimonial-name"><b>- SAM REYES,</b>Customer</p>
  <svg class="abs slide-arrow" style="left:120px" width="34" height="68" viewBox="0 0 34 68"><path d="M32 2L2 34l30 32" stroke="#fff" stroke-width="1.5" fill="none"/></svg>
  <svg class="abs slide-arrow" style="left:1046px" width="34" height="68" viewBox="0 0 34 68"><path d="M2 2l30 32L2 66" stroke="#fff" stroke-width="1.5" fill="none"/></svg>
</section>

<section class="contact">
  <h2 class="abs heading" style="top:2884px"><span class="accent">Get</span> in Touch</h2>
  <svg class="abs swoosh" style="top:2952px" width="74" height="22" viewBox="0 0 74 22"><path d="M2 20 Q30 2 72 4 Q34 6 2 20Z" fill="#5ab52f"/></svg>
  <form class="abs contact-form">
    <div class="field">First Name</div>
    <div class="field">Last Name</div>
    <div class="field">Email address</div>
    <div class="field">Phone Number</div>
    <div class="field field-message">Message</div>
  </form>
  <div class="abs grass" role="img" aria-label="Illustrated band of grass blades"></div>
  <a class="abs btn btn-submit">Submit Message</a>
</section>

<footer class="abs site-footer"></footer>
<div class="abs footer-brand">Brackwell<small>Landscapes</small></div>
<nav class="abs footer-nav"><span>HOME</span><span>/</span><span>ABOUT US</span><span>/</span><span>SERVICES</span><span>/</span><span>GALLERY</span><span>/</span><span>CONTACT US</span></nav>
<p class="abs footer-copy">© 2020 Brackwell Landscapes.All Rights Reserved &nbsp;|&nbsp; Privacy Policy</p>
<div class="abs social" aria-label="Social media links"><span></span><span></span><span></span></div>

</body>
</html>
```